Trevani.com- International Goal Achievement Coach Needs Website Design

I need a web design for my new company called Trevani. I help people who are stuck, people who have a big dream, but don't know how to get there. I help them to break their dreams down into small, manageable steps... and then I'm the "kick in the shin" to get them moving and thriving!

We can all be better- We can all DO better. I inspire people to Go Boldly in the direction of your dreams.

I have uploaded my logo along with some vintage champagne posters. Please use the vintage posters as inspiration. I like the bold, vintage look and feel. I would love the main colors of the design to be black, white and metallic gold. And to follow along this vintage look and feel. Please feel free to use the logo in black or metallic gold or white.

Target Market(s)

websites that I like- lunabrask.com & tessak.tv

I would like to also use the vintage champagne photos attached as inspiration as well.

Industry/Entity Type

It Company

Requirements
Must have
• Tabs should include: About, Work With Me, Praise, Giving Back

On the homepage add:
* Sign up for newsletter with space to enter name and email (No click throughs)
* Upcoming Events/Sessions
* Newsletter Posts
* Resources
* Praise Section

* Large photo on top with additional photos throughout the page/site.
Nice to have
• Any additions you can bring to the table would be greatly appreciated.

```html
<!DOCTYPE html>
<html lang="en">
<head>
<meta charset="utf-8">
<title>Trevani — Go Boldly</title>
<link href="https://fonts.googleapis.com/css2?family=Open+Sans:wght@400;600;700&display=swap" rel="stylesheet">
<style>
:root{
  --black:#141210;
  --black-soft:#2a2622;
  --cream:#f4ead2;
  --gold-dark:#9c7a2c;
  --gold:#c9a44e;
  --gold-light:#e7cf88;
  --gold-pale:#f1e2b0;
  --ink:#2b2b2b;
  --muted:#777;
  --title:#8a6a1f;
  --line:#e6e0d2;
  --white:#fff;
}
*{box-sizing:border-box;margin:0;padding:0}
html,body{width:1200px;height:2808px;overflow:hidden}
body{font-family:"Open Sans",Arial,sans-serif;color:var(--ink);position:relative;
  background:linear-gradient(160deg,var(--gold) 0%,var(--gold-light) 45%,var(--gold) 75%,var(--gold-light) 100%)}
.abs{position:absolute}

/* header */
.hero{left:0;top:0;width:1200px;height:624px;
  background:linear-gradient(180deg,#a9cde0 0%,#cfdfe2 35%,#d8b79a 60%,#c79a78 100%)}
.hero-strip{left:0;top:624px;width:1200px;height:18px;background:var(--cream)}
.logo{left:455px;top:-150px;width:290px;height:290px;border-radius:50%;background:var(--white);
  display:flex;align-items:flex-end;justify-content:center;padding-bottom:70px;gap:12px}
.logo-dot{width:46px;height:46px;border-radius:50%;background:var(--gold-dark)}
.logo-name{font-size:30px;color:var(--black);font-weight:400;line-height:46px}
.arrow{width:54px;height:54px;top:282px}

/* navigation */
.nav{left:0;top:642px;width:1200px;height:64px;background:var(--black)}
.nav a{position:absolute;top:21px;color:var(--white);text-decoration:none;font-size:17px;line-height:22px;transform:translateX(-50%);white-space:nowrap}
.nav a.active{color:var(--gold-light)}

.section-title{left:101px;top:764px;font-size:22px;font-weight:600;color:var(--black);letter-spacing:.5px}

/* posts */
.post{left:103px;width:648px;height:446px;background:var(--white);box-shadow:0 2px 4px rgba(0,0,0,.18)}
.post-img{position:absolute;left:11px;top:11px;width:626px;height:217px}
.date{position:absolute;left:11px;top:11px;width:60px;height:64px;background:var(--black);color:var(--white);text-align:center;font-size:12px;line-height:1.15;padding-top:5px}
.date b{display:block;font-size:21px;font-weight:600;color:var(--gold-light)}
.post h2{position:absolute;left:22px;top:258px;font-size:16px;font-weight:400;color:var(--title);text-transform:uppercase;letter-spacing:.3px;white-space:nowrap}
.meta{position:absolute;left:22px;top:291px;font-size:12.5px;color:#444;white-space:nowrap}
.meta span{padding:0 10px;border-left:1px solid #ccc}
.meta span:first-child{padding-left:0;border:0}
.excerpt{position:absolute;left:22px;top:320px;width:590px;font-size:12.5px;line-height:19px;color:var(--muted)}
.post hr{position:absolute;left:0;top:396px;width:100%;border:0;border-top:1px solid var(--line)}
.share{position:absolute;top:413px;display:flex;gap:4px;align-items:center}
.btn{font-size:11px;font-weight:700;padding:2px 7px;border-radius:3px;border:1px solid #d8ccaa;background:#f7f1e0;color:var(--black)}
.btn.like{background:var(--black);color:var(--gold-light);border-color:var(--black)}
.btn.plus{background:#fff;color:var(--gold-dark);border-color:#ddd}
.count{font-size:11px;border:1px solid #ccc;padding:1px 6px;color:#555;background:#fff}

/* sidebar */
.widget{left:788px;width:315px;background:var(--white);box-shadow:0 3px 3px rgba(0,0,0,.14)}
.w-head{position:absolute;left:22px;top:24px;display:flex;align-items:center;gap:18px;width:272px;border-bottom:1px solid var(--line);padding-bottom:12px}
.w-icon{width:38px;height:48px;background:var(--black);display:flex;flex-direction:column;justify-content:center;align-items:center;gap:3px}
.w-icon i{display:block;width:12px;height:2px;background:var(--gold-light)}
.w-head h3{font-size:19px;font-weight:400;color:var(--black);white-space:nowrap}
.events{position:absolute;left:22px;top:100px;width:272px;list-style:none}
.events li{font-size:11px;color:#666;height:30.5px;display:flex;justify-content:space-between;align-items:center;border-bottom:1px solid var(--line);padding-left:22px;position:relative;white-space:nowrap}
.events li::before{content:"";position:absolute;left:0;top:11px;width:11px;height:8px;background:repeating-linear-gradient(180deg,var(--gold-dark) 0 2px,transparent 2px 3px)}
.events li.on{color:var(--title);font-weight:600}
.events li em{font-style:normal;color:#aaa}
.field{position:absolute;left:22px;width:272px;height:32px;background:#f4f1ea;border:1px solid #e2dccd;display:flex;align-items:center;font-size:11px;color:#999;padding-left:12px;font-style:italic}
.praise{position:absolute;left:22px;width:272px;display:flex;gap:16px;border-bottom:1px solid var(--line);height:78px}
.praise .thumb{width:112px;height:60px;flex:none}
.praise p{font-size:11px;line-height:17px;color:#444;font-style:italic}
.praise small{font-size:9px;color:var(--title);display:block;font-style:normal}
.tile{position:absolute;width:131px;height:131px;border-radius:6px}
.more{position:absolute;left:0;width:100%;top:750px;text-align:center;font-size:15px;font-weight:600;color:var(--title)}

/* footer */
.footer{left:0;top:2709px;width:1200px;height:99px;background:linear-gradient(180deg,var(--black-soft),var(--black));border-top:3px solid var(--gold)}
.f-nav{position:absolute;left:0;top:17px;width:100%;display:flex;justify-content:center;gap:26px;font-size:11.5px;color:var(--white)}
.copy{position:absolute;left:101px;top:66px;font-size:12px;color:var(--gold-pale)}
.social{position:absolute;right:96px;top:62px;display:flex;gap:14px}
.social i{display:block;width:22px;height:22px;border-radius:50%;background:var(--gold-light)}
</style>
</head>
<body>

<div class="abs hero" role="img" aria-label="Large header photo of smiling friends gathered around a tablet outdoors on a sunny day"></div>
<div class="abs hero-strip"></div>
<div class="abs logo"><span class="logo-dot"></span><span class="logo-name">Trevani</span></div>
<svg class="abs arrow" style="left:35px" viewBox="0 0 54 54"><circle cx="27" cy="27" r="25" fill="rgba(255,255,255,.25)" stroke="#fff" stroke-width="2"/><path d="M31 17 21 27l10 10" fill="none" stroke="#fff" stroke-width="3"/></svg>
<svg class="abs arrow" style="left:1111px" viewBox="0 0 54 54"><circle cx="27" cy="27" r="25" fill="rgba(255,255,255,.25)" stroke="#fff" stroke-width="2"/><path d="M23 17l10 10-10 10" fill="none" stroke="#fff" stroke-width="3"/></svg>

<nav class="abs nav">
  <a class="active" style="left:125px">Home</a>
  <a style="left:247px">About</a>
  <a style="left:383px">Work with me</a>
  <a style="left:514px">Events</a>
  <a style="left:624px">Praise</a>
  <a style="left:746px">Giving Back</a>
  <a style="left:894px">Resources</a>
  <a style="left:1056px">Contact us</a>
</nav>

<h1 class="abs section-title">NEWSLETTER POSTS</h1>

<article class="abs post" style="top:812px">
  <div class="post-img" role="img" aria-label="Photo of a young woman with long hair looking down" style="background:linear-gradient(90deg,#e9e2dc,#c9a185 45%,#efe9e4)"></div>
  <div class="date">Dec<b>20</b>2014</div>
  <h2>I want to make my own decisions about end of life care</h2>
  <div class="meta"><span>By: Admin</span><span>WRITTEN IN GOAL SETTING</span><span>17 comments</span></div>
  <p class="excerpt">Lorem ipsum dolor sit amet, consectetuer adipiscing elit, sed diam nonummy nibh euismod ut laoreet dolore magna aliquam erat volutpat. Ut wisi enim ad minim veniam, quis nostrud ullamcorper suscipit lobortis nisl ut aliquip ex ea commodo consequat.</p>
  <hr>
  <div class="share" style="left:330px"><span class="btn">Share</span><span class="count">0</span></div>
  <div class="share" style="left:447px"><span class="btn like">Like</span><span class="count">0</span></div>
  <div class="share" style="left:563px"><span class="btn plus">+1</span><span class="count">0</span></div>
</article>

<article class="abs post" style="top:1277px">
  <div class="post-img" role="img" aria-label="Photo of a smiling woman with a camera against evening city lights" style="background:linear-gradient(90deg,#3a2212,#b48a34 35%,#6b4a22 60%,#2a1a14)"></div>
  <div class="date">Dec<b>20</b>2014</div>
  <h2>Truly listening to your patients</h2>
  <div class="meta"><span>By: Admin</span><span>WRITTEN IN GOAL SETTING</span><span>17 comments</span></div>
  <p class="excerpt">Lorem ipsum dolor sit amet, consectetuer adipiscing elit, sed diam nonummy nibh euismod tincidunt ut laoreet dolore magna aliquam erat volutpat. Ut wisi enim ad minim veniam, quis nostrud exerci tation ullamcorper suscipit lobortis nisl ut aliquip ex ea commodo consequat.</p>
  <hr>
  <div class="share" style="left:330px"><span class="btn">Share</span><span class="count">0</span></div>
  <div class="share" style="left:447px"><span class="btn like">Like</span><span class="count">0</span></div>
  <div class="share" style="left:563px"><span class="btn plus">+1</span><span class="count">0</span></div>
</article>

<article class="abs post" style="top:1737px">
  <div class="post-img" role="img" aria-label="Photo of a happy family of four outdoors in a garden" style="background:linear-gradient(90deg,#6f8f3c,#d9b79b 40%,#e8ddd2 65%,#7b9a4a)"></div>
  <div class="date">Dec<b>20</b>2014</div>
  <h2>She was in the other room, breathing in and out.</h2>
  <div class="meta"><span>By: Admin</span><span>WRITTEN IN GOAL SETTING</span><span>17 comments</span></div>
  <p class="excerpt">Lorem ipsum dolor sit amet, consectetuer adipiscing elit, sed diam nonummy nibh euismod tincidunt ut laoreet dolore magna aliquam erat volutpat. Ut wisi enim ad minim veniam, quis nostrud exerci tation ullamcorper suscipit lobortis nisl ut aliquip ex ea commodo consequat.</p>
  <hr>
  <div class="share" style="left:330px"><span class="btn">Share</span><span class="count">0</span></div>
  <div class="share" style="left:447px"><span class="btn like">Like</span><span class="count">0</span></div>
  <div class="share" style="left:563px"><span class="btn plus">+1</span><span class="count">0</span></div>
</article>

<article class="abs post" style="top:2200px">
  <div class="post-img" role="img" aria-label="Photo of a group fitness class stretching in a bright studio" style="background:linear-gradient(90deg,#d8d2cc,#c7a893 45%,#c98a7a 60%,#ded6cf)"></div>
  <div class="date">Dec<b>20</b>2014</div>
  <h2>She was in the other room, breathing in and out.</h2>
  <div class="meta"><span>By: Admin</span><span>WRITTEN IN GOAL SETTING</span><span>17 comments</span></div>
  <p class="excerpt">Lorem ipsum dolor sit amet, consectetuer adipiscing elit, sed diam nonummy nibh euismod tincidunt ut laoreet dolore magna aliquam erat volutpat. Ut wisi enim ad minim veniam, quis nostrud exerci tation ullamcorper suscipit lobortis nisl ut aliquip ex ea commodo consequat.</p>
  <hr>
  <div class="share" style="left:330px"><span class="btn">Share</span><span class="count">0</span></div>
  <div class="share" style="left:447px"><span class="btn like">Like</span><span class="count">0</span></div>
  <div class="share" style="left:563px"><span class="btn plus">+1</span><span class="count">0</span></div>
</article>

<aside class="abs widget" style="top:762px;height:292px">
  <div class="w-head"><div class="w-icon"><i></i><i></i><i></i></div><h3>UPCOMING EVENTS</h3></div>
  <ul class="events">
    <li>GO BOLDLY WORKSHOP<em>JAN 14</em></li>
    <li>DREAM MAPPING SESSION<em>JAN 28</em></li>
    <li class="on">GOAL SETTING DAY<em>FEB 07</em></li>
    <li>SMALL STEPS WEBINAR<em>FEB 19</em></li>
    <li>WOMEN WHO THRIVE<em>MAR 04</em></li>
    <li>SPRING RETREAT<em>MAR 21</em></li>
  </ul>
</aside>

<aside class="abs widget" style="top:1078px;height:185px">
  <div class="w-head"><div class="w-icon"><i></i><i></i><i></i></div><h3>NEWSLETTER</h3></div>
  <div class="field" style="top:98px">Your name</div>
  <div class="field" style="top:138px">Your email</div>
</aside>

<aside class="abs widget" style="top:1287px;height:346px">
  <div class="w-head"><div class="w-icon"><i></i><i></i><i></i></div><h3>PRAISE</h3></div>
  <div class="praise" style="top:100px"><div class="thumb" role="img" aria-label="Client portrait photo" style="background:linear-gradient(90deg,#bbb,#555,#999)"></div><p>"She gave me the kick I needed to start."<small>Anna R. | Coaching client</small></p></div>
  <div class="praise" style="top:180px"><div class="thumb" role="img" aria-label="Client portrait photo" style="background:linear-gradient(90deg,#ddd,#888,#eee)"></div><p>"My big dream now has a clear plan."<small>Mark T. | Workshop guest</small></p></div>
  <div class="praise" style="top:260px;border:0"><div class="thumb" role="img" aria-label="Client portrait photo" style="background:linear-gradient(90deg,#555,#aaa,#666)"></div><p>"Bold, warm and truly inspiring."<small>Lena P. | Coaching client</small></p></div>
</aside>

<aside class="abs widget" style="top:1655px;height:788px;background:#f6f1e4">
  <div class="tile" style="left:17px;top:19px;background:var(--black)" role="img" aria-label="Resource guide cover"></div>
  <div class="tile" style="left:165px;top:19px;background:linear-gradient(135deg,var(--gold-dark),var(--gold-light))" role="img" aria-label="Resource guide cover"></div>
  <div class="tile" style="left:17px;top:167px;background:linear-gradient(135deg,var(--gold-light),var(--gold-dark))" role="img" aria-label="Resource guide cover"></div>
  <div class="tile" style="left:165px;top:167px;background:var(--black-soft)" role="img" aria-label="Resource guide cover"></div>
  <div class="tile" style="left:17px;top:315px;background:var(--cream);border:1px solid #e2d6b4" role="img" aria-label="Resource guide cover"></div>
  <div class="tile" style="left:165px;top:315px;background:var(--black)" role="img" aria-label="Resource guide cover"></div>
  <div class="tile" style="left:17px;top:462px;background:var(--black-soft)" role="img" aria-label="Resource guide cover"></div>
  <div class="tile" style="left:165px;top:462px;background:linear-gradient(135deg,var(--gold),var(--gold-pale))" role="img" aria-label="Resource guide cover"></div>
  <div class="tile" style="left:17px;top:610px;background:linear-gradient(135deg,var(--gold-dark),var(--black))" role="img" aria-label="Resource guide cover"></div>
  <div class="more">All Resources</div>
</aside>

<footer class="abs footer">
  <div class="f-nav"><span>HOME</span><span>ABOUT TESSA</span><span>WORK WITH ME</span><span>EVENTS</span><span>PRAISE</span><span>GIVING BACK</span><span>RESOURCES</span><span>CONTACT</span></div>
  <div class="copy">Yoursite © 2014 All Rights Reserved.</div>
  <div class="social"><i></i><i></i><i></i></div>
</footer>

</body>
</html>
```